High Tech Real Estate Startup needs a business card

We are developing an innovative real estate marketing product based around advanced search and virtual reality.

We talk to people, we need business cards.

Target Market(s)

The target market is technology professionals and realtors.

Contact Information for Business Card

The information to be included will include

Name
Title
Phone Number
E-mail Address
www.zelquin.com

It should use simple iconography for each one of those fields.

Font styles to use
Other font styles liked:
• Co, Jubilat, Avenir

Colors

Designer to choose colors to be used in the design.

Requirements
Must have
• Clean aesthetic,
• Good use of negative space.
• It should use our company logo, shown in the attached file. It is able to use the negative of that logo (coloured font and white background) and I have attached other acceptable accent colours in a swatch file.
Should not have
• Should not be too busy
• No extraneous text (slogans, tag lines etc)

```html
<!DOCTYPE html>
<html lang="en">
<head>
<meta charset="utf-8">
<title>Zelquin Business Card</title>
<link rel="stylesheet" href="https://fonts.googleapis.com/css2?family=Nunito+Sans:wght@400;600&display=swap">
<style>
  :root {
    --teal: #08bac0;
    --white: #ffffff;
    --ink: #55666c;
    --backdrop: #e4e5e6;
    --shadow: rgba(0, 0, 0, 0.18);
  }
  * { margin: 0; padding: 0; box-sizing: border-box; }
  html, body {
    width: 1200px;
    height: 1000px;
    overflow: hidden;
    background: var(--backdrop);
    font-family: "Nunito Sans", "Avenir", sans-serif;
  }
  .canvas { position: relative; width: 1200px; height: 1000px; }

  .card {
    position: absolute;
    background: var(--white);
    border-radius: 40px;
    overflow: hidden;
    box-shadow: 0 6px 18px var(--shadow);
  }

  /* Front */
  .card-front {
    left: 152px; top: 102px;
    width: 626px; height: 358px;
    display: flex; align-items: center; justify-content: center;
  }
  .wordmark {
    color: var(--teal);
    font-weight: 600;
    letter-spacing: 1px;
    line-height: 1;
  }
  .card-front .wordmark { font-size: 86px; }

  /* Back */
  .card-back {
    left: 372px; top: 548px;
    width: 630px; height: 360px;
  }
  .identity-band {
    position: absolute; left: 0; top: 0;
    width: 100%; height: 202px;
    background: var(--teal);
    color: var(--white);
  }
  .person-name {
    position: absolute; left: 36px; top: 104px;
    font-size: 31px; font-weight: 400; line-height: 1;
  }
  .person-title {
    position: absolute; left: 36px; top: 148px;
    font-size: 18px; font-weight: 400; line-height: 1;
  }
  .contact-list {
    position: absolute; left: 34px; top: 232px;
    list-style: none;
  }
  .contact-item {
    display: flex; align-items: center;
    height: 29px;
    color: var(--ink);
    font-size: 21px;
    letter-spacing: 2px;
  }
  .contact-icon {
    width: 18px; height: 18px;
    margin-right: 22px;
    fill: var(--ink);
  }
  .card-back .wordmark {
    position: absolute; right: 50px; top: 270px;
    font-size: 44px;
  }
</style>
</head>
<body>
<main class="canvas">
  <section class="card card-front">
    <span class="wordmark">ZELQUIN</span>
  </section>

  <section class="card card-back">
    <div class="identity-band">
      <p class="person-name">Name of Person</p>
      <p class="person-title">Title of Person</p>
    </div>

    <ul class="contact-list">
      <li class="contact-item">
        <svg class="contact-icon" viewBox="0 0 24 24" aria-hidden="true">
          <path d="M6.6 10.8c1.4 2.8 3.8 5.1 6.6 6.6l2.2-2.2c.3-.3.7-.4 1-.2 1.1.4 2.3.6 3.6.6.6 0 1 .4 1 1V20c0 .6-.4 1-1 1C10.6 21 3 13.4 3 4c0-.6.4-1 1-1h3.5c.6 0 1 .4 1 1 0 1.3.2 2.5.6 3.6.1.3 0 .7-.2 1L6.6 10.8z"/>
        </svg>
        <span>+123 456 7890</span>
      </li>
      <li class="contact-item">
        <svg class="contact-icon" viewBox="0 0 24 24" aria-hidden="true">
          <path d="M12 2a10 10 0 1 0 0 20 10 10 0 0 0 0-20zm6.9 6h-2.9a15.7 15.7 0 0 0-1.4-3.6A8 8 0 0 1 18.9 8zM12 4c.8 1.2 1.5 2.5 1.9 4h-3.8c.4-1.5 1.1-2.8 1.9-4zM4.3 14a8 8 0 0 1 0-4h3.4a16 16 0 0 0 0 4H4.3zm.8 2h2.9c.3 1.3.8 2.5 1.4 3.6A8 8 0 0 1 5.1 16zM8 8H5.1a8 8 0 0 1 4.3-3.6C8.8 5.5 8.3 6.7 8 8zm4 12c-.8-1.2-1.5-2.5-1.9-4h3.8c-.4 1.5-1.1 2.8-1.9 4zm2.3-6H9.7a14 14 0 0 1 0-4h4.6a14 14 0 0 1 0 4zm.3 5.6c.6-1.1 1.1-2.3 1.4-3.6h2.9a8 8 0 0 1-4.3 3.6zm1.7-5.6a16 16 0 0 0 0-4h3.4a8 8 0 0 1 0 4h-3.4z"/>
        </svg>
        <span>www.zelquin.com</span>
      </li>
      <li class="contact-item">
        <svg class="contact-icon" viewBox="0 0 24 24" aria-hidden="true">
          <path d="M3 5h18v2.2l-9 5.6-9-5.6V5zm0 4.6l9 5.6 9-5.6V19H3V9.6z"/>
        </svg>
        <span>E-mail Address</span>
      </li>
    </ul>

    <span class="wordmark">ZELQUIN</span>
  </section>
</main>
</body>
</html>
```